business card deign

Logo needs the following on it.
1. attached logo
2. Tagline - "Cold drinks, loud music, long nights...that's what we do!"
3. Name- Dalton Pikes, Founder and CPO
4. Address - 412 E. Carver Avenue, Ste 2207, Tampa, FL. 33917
5. Phone - 555.318.4726

```html
<!DOCTYPE html>
<html lang="en">
<head>
<meta charset="utf-8">
<title>Kelvo business card</title>
<link href="https://fonts.googleapis.com/css2?family=Montserrat:wght@400;500;700&display=swap" rel="stylesheet">
<style>
:root{
  --backdrop:#9b9b9b;
  --card-light:#ffffff;
  --card-dark:#1e1e1e;
  --ink:#111111;
  --ink-soft:#222222;
  --mark-dark:#0d0d0d;
  --tagline:#dcdcdc;
}
*{margin:0;padding:0;box-sizing:border-box}
html,body{width:1093px;height:1200px;overflow:hidden;background:var(--backdrop);font-family:"Montserrat",sans-serif}
.canvas{position:relative;width:1093px;height:1200px}
.card{position:absolute;left:265px;width:580px;border-radius:18px;box-shadow:2px 4px 6px rgba(0,0,0,.45);overflow:hidden}
.card--front{top:225px;height:363px;background:var(--card-light);color:var(--ink)}
.card--back{top:616px;height:366px;background:var(--card-dark)}
.person{position:absolute;left:28px;top:55px}
.person__name{font-weight:700;font-size:22px;line-height:1;letter-spacing:.1px}
.person__title{font-weight:400;font-size:13px;margin-top:5px;color:var(--ink-soft)}
.brand{position:absolute;font-weight:700;text-transform:uppercase;line-height:1;white-space:nowrap}
.brand--front{right:20px;top:118px;font-size:26px;letter-spacing:14px;color:var(--ink)}
.brand--back{left:0;right:0;top:225px;text-align:center;font-size:42px;letter-spacing:26px;padding-left:26px;color:var(--mark-dark)}
.contacts{position:absolute;left:29px;top:261px;list-style:none}
.contacts li{display:flex;align-items:center;height:26px;font-size:14px;color:var(--ink-soft)}
.contacts svg{width:13px;height:13px;margin-right:8px;fill:var(--ink)}
.address{position:absolute;left:365px;top:297px;font-size:13.5px;line-height:16.5px;font-style:normal;color:var(--ink-soft);white-space:nowrap}
.tagline{position:absolute;left:0;right:0;top:317px;text-align:center;font-size:13.5px;color:var(--tagline)}
</style>
</head>
<body>
<div class="canvas">
  <section class="card card--front">
    <div class="person">
      <h1 class="person__name">Dalton Pikes</h1>
      <p class="person__title">Founder and CPO</p>
    </div>
    <div class="brand brand--front">Kelvo</div>
    <ul class="contacts">
      <li><svg viewBox="0 0 24 24"><path d="M6.6 10.8a15.1 15.1 0 0 0 6.6 6.6l2.2-2.2c.3-.3.7-.4 1-.2 1.1.4 2.3.6 3.6.6.6 0 1 .4 1 1V20c0 .6-.4 1-1 1A17 17 0 0 1 3 4c0-.6.4-1 1-1h3.5c.6 0 1 .4 1 1 0 1.3.2 2.5.6 3.6.1.3 0 .7-.2 1z"/></svg>555.318.4726</li>
      <li><svg viewBox="0 0 24 24"><path d="M2 5h20v2l-10 6L2 7z"/><path d="M2 9l10 6 10-6v10H2z"/></svg>info@kelvo.com</li>
      <li><svg viewBox="0 0 24 24"><circle cx="12" cy="12" r="10"/><path d="M7 6c2 1 2 3 4 3s1 3-1 3-3 2-2 5M16 5c-1 2 0 3 2 3M14 14c2 0 3 1 3 3" stroke="#fff" stroke-width="1.6" fill="none"/></svg>www.kelvo.com</li>
    </ul>
    <address class="address">412 E. Carver Avenue, Ste 2207,<br>Tampa, FL. 33917</address>
  </section>
  <section class="card card--back">
    <div class="brand brand--back">Kelvo</div>
    <p class="tagline">Cold drinks, loud music, long nights...that's what we do</p>
  </section>
</div>
</body>
</html>
```